Brightwave Reach - Business Card

We need a business card for a Social Media Marketing company that specializes in online marketing for small businesses in Canada using common Social Media platforms such as Pixlora, Chatterly, Blinkpost & Quibber.

I have uploaded a copy of our logo which I would like utilized in the business card. We would like the business card to be modern yet classy design.

Our website is www.brightwavereach.ca

Industry/Entity Type

Marketing

Contact Information for Business Card

Email: info@brightwavereach.ca
Website: www.brightwavereach.ca
Telephone: 604-555-0193

Colors

Designer to choose colors to be used in the design.

Requirements
Must have
• Social Media icons on reverse
• Please add some designs with color.

```html
<!DOCTYPE html>
<html lang="en">
<head>
<meta charset="utf-8">
<title>Brightwave Reach – Business Card</title>
<link href="https://fonts.googleapis.com/css2?family=Roboto:wght@400;500;700&display=swap" rel="stylesheet">
<style>
  :root {
    --stage: #2b2b2c;
    --paper: #f1f1f1;
    --slate: #3d4043;
    --slate-deep: #36393c;
    --ink: #4a4a4a;
    --white: #ffffff;
    --rule: #9a9c9e;
  }
  * { margin: 0; padding: 0; box-sizing: border-box; }
  html, body {
    width: 1200px; height: 960px; overflow: hidden;
    background: var(--stage);
    font-family: "Roboto", Arial, sans-serif;
  }
  .canvas { position: relative; width: 1200px; height: 960px; }

  .card-front {
    position: absolute; left: 314px; top: 113px;
    width: 600px; height: 343px;
    background: var(--paper);
  }
  .front-band {
    position: absolute; left: 0; top: 54px;
    width: 100%; height: 121px;
    background: var(--slate);
  }
  .holder { position: absolute; left: 47px; top: 38px; color: var(--white); }
  .holder-name { font-size: 20px; font-weight: 500; letter-spacing: 0.3px; }
  .holder-role { font-size: 15px; font-weight: 500; margin-top: 3px; }
  .front-brand {
    position: absolute; right: 44px; top: 28px; width: 190px;
    color: var(--white); font-weight: 700; font-size: 26px;
    line-height: 30px; text-align: center; text-transform: uppercase;
  }
  .contact-list {
    position: absolute; left: 48px; top: 240px;
    list-style: none; color: var(--ink); font-size: 15px;
  }
  .contact-list li { display: flex; align-items: center; height: 19px; }
  .contact-list svg { width: 13px; height: 13px; margin-right: 9px; fill: var(--ink); }

  .card-back {
    position: absolute; left: 311px; top: 472px;
    width: 600px; height: 342px;
    background: radial-gradient(ellipse at 50% 40%, #44474a 0%, var(--slate-deep) 75%);
  }
  .back-brand {
    position: absolute; left: 0; top: 118px; width: 100%;
    color: var(--white); font-weight: 700; font-size: 36px;
    line-height: 42px; text-align: center; text-transform: uppercase;
  }
  .social-row {
    position: absolute; left: 0; top: 285px; width: 100%;
    display: flex; align-items: center; justify-content: center; gap: 10px;
    color: var(--white); font-size: 13px;
  }
  .social-rule { width: 90px; height: 1px; background: linear-gradient(90deg, transparent, var(--rule), transparent); }
  .social-item { display: flex; align-items: center; gap: 5px; }
  .social-dot { width: 12px; height: 12px; border: 1.5px solid var(--white); border-radius: 50%; }
</style>
</head>
<body>
<div class="canvas">

  <section class="card-front">
    <div class="front-band">
      <div class="holder">
        <div class="holder-name">DANIEL HART</div>
        <div class="holder-role">CEO/FOUNDER</div>
      </div>
      <div class="front-brand">Brightwave Reach</div>
    </div>
    <ul class="contact-list">
      <li>
        <svg viewBox="0 0 24 24"><path d="M6.6 10.8a15.2 15.2 0 0 0 6.6 6.6l2.2-2.2a1 1 0 0 1 1-.25 11.4 11.4 0 0 0 3.6.57 1 1 0 0 1 1 1V20a1 1 0 0 1-1 1A17 17 0 0 1 3 4a1 1 0 0 1 1-1h3.5a1 1 0 0 1 1 1c0 1.25.2 2.45.57 3.57a1 1 0 0 1-.25 1z"/></svg>
        604-555-0193
      </li>
      <li>
        <svg viewBox="0 0 24 24"><path d="M2 5h20v14H2z M4 7v.4l8 5 8-5V7l-8 5z" fill-rule="evenodd"/></svg>
        info@brightwavereach.ca
      </li>
      <li>
        <svg viewBox="0 0 24 24"><path d="M12 2a10 10 0 1 0 0 20 10 10 0 0 0 0-20zm-1 17.9A8 8 0 0 1 4.1 10H7l2 2v1.5l2 2zm6.9-2.5A2 2 0 0 0 16 16h-1v-3a1 1 0 0 0-1-1H8v-2h2a1 1 0 0 0 1-1V7h2a2 2 0 0 0 2-2v-.4a8 8 0 0 1 2.9 12.8z"/></svg>
        www.brightwavereach.ca
      </li>
    </ul>
  </section>

  <section class="card-back">
    <div class="back-brand">Brightwave<br>Reach</div>
    <div class="social-row">
      <span class="social-rule"></span>
      <span class="social-item"><span class="social-dot"></span>Chatterly</span>
      <span class="social-item"><span class="social-dot"></span>Pixlora</span>
      <span class="social-item"><span class="social-dot"></span>Quibber</span>
      <span class="social-rule"></span>
    </div>
  </section>

</div>
</body>
</html>
```